Label design - Superfood blend

We are a family owned nutrition company with big ambitions. Our goal is to develop a range of 100% natural supplements for women, inspired by nature & modern technology that helps them meet their nutritional needs while nourishing them from within. All our products are junk free because we believe that that’s how nature intended it. We also produce products through a sustainable process and only use biodegradable packaging for our products (See link - https://www.loamwrap.org.uk/biodegradable-stand-pouch-250g-kraft)

Our brand style is modern and minimalist. This same style will be reflected in our social media, website and we want it to be represented through the label designs for our product packaging.

We want some creative designers to design a label that is true to our style (See attached packaging brief with designs we like) and displays our values of Premium, High Quality, Organic Real Food supplements focused on women. I have provided examples in the attached brief, but please only use as inspiration, I dont want any of them to be copied (sorry have had my fingers burnt already !)
Updates

Hello all, Please note this design is for a LABEL and not the whole package. We will have a 500gm biodegradable brown package, and we will have a label (which is what this project is about) that will be stuck on the front. The size of the label will be a rectangle (unless you come up with a new shape) in the size 20cm * 15cm. Please do not submit designs for the WHOLE from of the package, as we dont intend to have printed packages. Regards

Hello all, I have added a new logo version to the attachments, could you please also try that version. Could you also please look at the new sliders. We are only looking for a minimlaist theme. If you dont know what that means, please do feel free to ask, I would be happy to supply examples. Minimalist designs, means clean, modern, upmarket, elegant designs. It does not use too many colors and mostly sticks to a combination of black and white with colors used sparingly. See some below for your reference anyway. https://www.pitchloft.co.uk/design/13359317 https://www.pitchloft.co.uk/design/17270649 https://www.pitchloft.co.uk/design/12584145 https://www.pitchloft.co.uk/design/12367479 https://www.snapquilt.com/search/pins/?q=minimalist%20label%20design&rs=rs&eq=&etslf=2809&term_meta[]=minimalist%7Crecentsearch%7Cundefined&term_meta[]=label%7Crecentsearch%7Cundefined&term_meta[]=design%7Crecentsearch%7Cundefined Regards

Target Market(s)

The target market is women between the age 25 to 45, based in UK (mostly based in larger cities in UK). They are typically middle class or higher and would be in demanding jobs and social lives, that requires for them to meet their nutrition needs in convenient, easy to take forms. The women would also be socially conscious and sensitive to issues like women's rights, environmental issues, healthy food, organic food and sustainability etc. I have a much more detailed customer avatar if required

Font styles to use
Serif
Sans Serif
Decorative
Script

Colors
e8e8e8
474747
1b1b1b
add136

Requirements
Must have
• The label, should look minimalist and modern, throw in some out of the box creativity and we have a winner. Creativity will definitely be of importance. Our packaging is a biodegradable brown paper stand up pouch (Example link in product description). So to make it standout from other colorful packaging - being creative would definitely help.
• Please use the color schemes provided in the brief (See attachments). But if you want to experiment I would be open to it, as long as they are still minimalist and does not stray very far from the color given in the brief :)

```html
<!DOCTYPE html>
<html lang="en">
<head>
<meta charset="utf-8">
<title>Veridano – Tend Thy Gut label set</title>
<link href="https://fonts.googleapis.com/css2?family=Montserrat:wght@300;400;600;800&family=Oswald:wght@400&display=swap" rel="stylesheet">
<style>
  :root{
    --paper:#ffffff;
    --light:#e8e8e8;
    --mid:#474747;
    --ink:#1b1b1b;
    --leaf:#add136;
    --vegan:#5aa05a;
    --grey:#8a8a8a;
  }
  *{margin:0;padding:0;box-sizing:border-box}
  html,body{width:1200px;height:857px;overflow:hidden;background:var(--paper)}
  body{position:relative;font-family:"Montserrat",sans-serif;color:var(--ink)}

  .label{position:absolute;top:369px;width:176px;height:240px;background:var(--light);border-radius:8px;overflow:hidden;box-shadow:0 1px 3px rgba(0,0,0,.12)}
  .label--one{left:133px}
  .label--two{left:390px}
  .label--three{left:649px}
  .label--four{left:907px}

  /* split variant */
  .split .strip{position:absolute;top:0;bottom:0;width:64px;background:linear-gradient(90deg,var(--ink),var(--mid) 70%,var(--ink))}
  .split .panel{position:absolute;top:0;bottom:0;width:112px;background:linear-gradient(180deg,#f4f4f4,var(--light));padding:0 10px}
  .label--one .strip{left:0} .label--one .panel{left:64px}
  .label--two .strip{right:0} .label--two .panel{left:0}
  .net{position:absolute;bottom:22px;width:64px;text-align:center;font-size:7.5px;font-weight:300;color:#d8d8d8;line-height:1.3}
  .label--one .net{left:0} .label--two .net{right:0}

  .brand{font-weight:400;letter-spacing:3px;font-size:10.5px;color:var(--ink)}
  .split .brand{margin-top:50px}
  .title-bold{font-weight:800;font-size:28px;line-height:1;margin-top:10px;letter-spacing:-.5px}
  .title-outline{font-weight:800;font-size:15px;line-height:1.1;color:transparent;-webkit-text-stroke:.7px var(--mid);letter-spacing:.5px}
  .rule{height:1px;background:var(--ink);margin:5px 0 4px}
  .kicker{font-size:7px;font-weight:800;letter-spacing:.2px}
  .blurb{margin-top:20px;font-size:4.6px;line-height:1.35;color:var(--mid);text-transform:uppercase}
  .badges{position:absolute;bottom:20px;display:flex;align-items:center;gap:18px}
  .split .badges{left:10px}
  .badge-organic{width:28px;height:28px;border-radius:50%;border:1.5px solid var(--mid)}
  .badge-vegan{width:22px;height:22px;border-radius:50%;border:1.5px solid var(--vegan)}

  /* banded variant */
  .banded{background:linear-gradient(180deg,#f6f6f6,var(--light))}
  .band{position:absolute;left:0;right:0;top:0;height:40px;background:var(--ink)}
  .frame{position:absolute;left:24px;top:22px;width:130px;height:54px;border:1px solid var(--ink);text-align:center}
  .frame .kicker{height:18px;line-height:18px;color:var(--paper);font-weight:600;font-size:6.5px;letter-spacing:.4px;border-bottom:1px solid var(--light)}
  .frame .brand{margin-top:10px;font-size:12px;letter-spacing:3.5px}
  .banded .title{position:absolute;top:102px;left:0;right:0;text-align:center;font-family:"Oswald",sans-serif;font-size:24px;letter-spacing:.5px;color:var(--ink)}
  .banded .sub{position:absolute;top:142px;left:0;right:0;text-align:center;font-size:7px;line-height:1.35;color:var(--grey);font-weight:400}
  .banded .badges{left:54px;bottom:32px}
  .netline{position:absolute;left:10px;right:10px;bottom:14px;text-align:center;font-size:5px;color:var(--mid);line-height:1.3}
  .netline::before{content:"";position:absolute;left:0;right:0;top:3px;height:1px;background:var(--mid);z-index:0}
  .netline span{position:relative;background:var(--light);padding:0 4px}
</style>
</head>
<body>

<article class="label split label--one">
  <div class="strip"></div>
  <div class="net">Net Weight<br>500 g</div>
  <div class="panel">
    <p class="brand">VERIDANO</p>
    <h1 class="title-bold">TEND</h1>
    <p class="title-outline">THY GUT</p>
    <div class="rule"></div>
    <p class="kicker">FOOD SUPPLEMENT</p>
    <p class="blurb">Organic<br>Plant-based prebiotics<br>and superfood blend</p>
    <div class="badges"><span class="badge-organic"></span><span class="badge-vegan"></span></div>
  </div>
</article>

<article class="label split label--two">
  <div class="panel">
    <p class="brand">VERIDANO</p>
    <h1 class="title-bold">TEND</h1>
    <p class="title-outline">THY GUT</p>
    <div class="rule"></div>
    <p class="kicker">FOOD SUPPLEMENT</p>
    <p class="blurb">Organic<br>Plant-based prebiotics<br>and superfood blend</p>
    <div class="badges"><span class="badge-organic"></span><span class="badge-vegan"></span></div>
  </div>
  <div class="strip"></div>
  <div class="net">Net Weight<br>500 g</div>
</article>

<article class="label banded label--three">
  <div class="band"></div>
  <div class="frame">
    <p class="kicker">FOOD SUPPLEMENT</p>
    <p class="brand">VERIDANO</p>
  </div>
  <h1 class="title">TEND THY GUT</h1>
  <p class="sub">Organic, Plant-Based Prebiotics<br>and Superfood Blend</p>
  <div class="badges"><span class="badge-organic"></span><span class="badge-vegan"></span></div>
  <p class="netline"><span>Net Weight</span><br><span>500 g</span></p>
</article>

<article class="label banded label--four">
  <div class="band"></div>
  <div class="frame">
    <p class="kicker">FOOD SUPPLEMENT</p>
    <p class="brand">VERIDANO</p>
  </div>
  <h1 class="title">TEND THY GUT</h1>
  <p class="sub">Organic, Plant-Based Prebiotics<br>and Superfood Blend</p>
  <div class="badges"><span class="badge-organic"></span><span class="badge-vegan"></span></div>
  <p class="netline"><span>Net Weight</span><br><span>500 g</span></p>
</article>

</body>
</html>
```